We need a new business card that reflects who we are. Professional, classy, modern, and service ori

We need a business card design for a window coverings design company in Kansas City called Bright Lane Interiors. We offer professional, modern, and high quality window covering products. We are looking to portray an image of a big, national franchise. We are a 5 location (with showrooms) business with 10 professional designers and 4 professional installers. These cards will be used with Thank you cards, given to realtors, and asked for referrals with.

Target Market(s)

Kansas City

Industry/Entity Type

Business

Contact Information for Business Card

We would like our card to look clean and simple on the front, featuring our logo and Marlow Fenwick's. Our designers' phone numbers and emails should be displayed as well as their title.

Font styles to use
Sans Serif

Colors

Designer to choose colors to be used in the design.

Requirements
Must have
• Front - Logos, name, phone number, email address
• Back - Showroom locations, social media? Appt date/time?
Nice to have
• I would like a clean and modern look (not contemporary. I like a white background, but I am open to ideas. Looking for a "National chain" look for a small business.
Should not have
• Too much busyness.

```html
<!DOCTYPE html>
<html lang="en">
<head>
<meta charset="utf-8">
<title>Bright Lane Interiors – Business Card</title>
<link rel="stylesheet" href="https://fonts.googleapis.com/css2?family=Roboto:wght@400;500;700&family=Roboto+Condensed:wght@500&family=Cormorant+Garamond:wght@500&display=swap">
<style>
  :root {
    --backdrop: #2b2b2b;
    --card: #f3f3f3;
    --red: #c8373b;
    --ink: #111111;
    --grey-text: #4a4a4a;
    --rule: #8a8a8a;
    --dots: #7a7a7a;
  }
  * { margin: 0; padding: 0; box-sizing: border-box; }
  html, body { width: 1200px; height: 960px; overflow: hidden; }
  body {
    background: var(--backdrop);
    font-family: "Roboto", Arial, sans-serif;
    position: relative;
  }
  .card {
    position: absolute;
    width: 600px;
    height: 342px;
    background: var(--card);
    overflow: hidden;
  }
  .card-front { left: 322px; top: 108px; }
  .card-back  { left: 320px; top: 493px; }

  /* Front */
  .brand {
    position: absolute;
    right: 27px;
    top: 52px;
    text-align: right;
  }
  .brand-name {
    display: flex;
    align-items: center;
    justify-content: flex-end;
    gap: 10px;
    font-weight: 700;
    font-size: 27px;
    color: var(--ink);
    letter-spacing: 0.2px;
  }
  .brand-mark {
    width: 22px; height: 22px;
    background: var(--red);
  }
  .brand-tagline {
    margin-top: 12px;
    font-family: "Cormorant Garamond", Georgia, serif;
    font-weight: 500;
    font-size: 13.5px;
    color: var(--ink);
  }
  .person {
    position: absolute;
    left: 28px;
    top: 206px;
  }
  .person-name {
    font-family: "Roboto Condensed", "Arial Narrow", sans-serif;
    font-weight: 500;
    font-size: 24px;
    color: var(--red);
    line-height: 1;
  }
  .person-title {
    margin-top: 6px;
    font-weight: 500;
    font-size: 14.5px;
    color: var(--ink);
  }
  .divider {
    position: absolute;
    left: 28px;
    top: 261px;
    width: 530px;
    height: 1px;
    background: var(--rule);
  }
  .contact {
    position: absolute;
    left: 28px;
    top: 273px;
    list-style: none;
    font-size: 14px;
    color: var(--grey-text);
  }
  .contact li { display: flex; align-items: center; gap: 8px; height: 20px; }
  .contact svg { width: 13px; height: 13px; fill: var(--red); }
  .website {
    position: absolute;
    right: 27px;
    top: 292px;
    font-size: 14.5px;
    letter-spacing: 0.3px;
    color: var(--grey-text);
  }
  .footer-band { position: absolute; left: 0; bottom: 0; width: 600px; height: 14px; }

  /* Back */
  .back-brand {
    position: absolute;
    left: 0; right: 0;
    top: 38px;
    display: flex;
    justify-content: center;
    align-items: center;
    gap: 8px;
    font-weight: 700;
    font-size: 26px;
    color: var(--ink);
  }
  .back-brand .brand-mark { width: 20px; height: 20px; }
  .appointment-title {
    position: absolute;
    left: 0; right: 0;
    top: 89px;
    text-align: center;
    font-weight: 500;
    font-size: 20px;
    color: var(--red);
  }
  .field {
    position: absolute;
    left: 43px;
    display: flex;
    align-items: baseline;
    font-size: 16px;
    color: var(--red);
  }
  .field-name { top: 139px; width: 497px; }
  .field-when { top: 180px; width: 500px; }
  .fill-line {
    flex: 1;
    border-bottom: 1px dotted var(--dots);
    margin: 0 4px 0 6px;
    height: 1px;
  }
  .field-when .fill-line.date { flex: 0 0 212px; margin-right: 2px; }
  .ampm { font-size: 13px; margin-left: 2px; }
  .locations {
    position: absolute;
    left: 0; right: 0;
    top: 232px;
    padding-left: 6px;
    text-align: center;
    font-weight: 700;
    font-size: 15px;
    color: var(--grey-text);
    letter-spacing: 0.1px;
    white-space: nowrap;
  }
  .social {
    position: absolute;
    left: 44px;
    top: 279px;
    display: flex;
    gap: 3px;
  }
  .social span {
    width: 22px; height: 22px;
    border-radius: 50%;
    background: var(--red);
  }
  .partner {
    position: absolute;
    right: 56px;
    top: 280px;
    font-weight: 700;
    font-size: 15px;
    color: var(--grey-text);
  }
</style>
</head>
<body>

<section class="card card-front">
  <div class="brand">
    <div class="brand-name"><span class="brand-mark"></span>Bright Lane Interiors</div>
    <div class="brand-tagline">Blinds, Shades, Shutters, Draperies &amp; Decor</div>
  </div>

  <div class="person">
    <div class="person-name">EVAN CARTER</div>
    <div class="person-title">DESIGNER</div>
  </div>

  <div class="divider"></div>

  <ul class="contact">
    <li>
      <svg viewBox="0 0 24 24" aria-hidden="true"><path d="M6.6 10.8c1.4 2.8 3.8 5.1 6.6 6.6l2.2-2.2c.3-.3.7-.4 1-.2 1.1.4 2.3.6 3.6.6.6 0 1 .4 1 1V20c0 .6-.4 1-1 1C10.6 21 3 13.4 3 4c0-.6.4-1 1-1h3.5c.6 0 1 .4 1 1 0 1.3.2 2.5.6 3.6.1.3 0 .7-.2 1z"/></svg>
      913.555.0148
    </li>
    <li>
      <svg viewBox="0 0 24 24" aria-hidden="true"><path d="M2 5h20v2l-10 7L2 7z"/><path d="M2 9l10 7 10-7v10H2z"/></svg>
      info@brightlaneinteriors.com
    </li>
  </ul>

  <div class="website">www.brightlaneinteriors.com</div>

  <svg class="footer-band" viewBox="0 0 600 14" aria-hidden="true">
    <polygon points="0,2 355,2 351,14 0,14" fill="var(--red)"/>
    <polygon points="355,2 359,2 355,14 351,14" fill="var(--card)"/>
    <polygon points="359,0 600,0 600,14 355,14" fill="var(--ink)"/>
  </svg>
</section>

<section class="card card-back">
  <div class="back-brand"><span class="brand-mark"></span>Bright Lane</div>
  <div class="appointment-title">Next Appointment</div>

  <div class="field field-name">Name :<span class="fill-line"></span></div>
  <div class="field field-when">Date :<span class="fill-line date"></span>Time :<span class="fill-line"></span><span class="ampm">AM/PM</span></div>

  <div class="locations">WESTBROOK | ASHFORD PARK | CEDAR RIDGE | NORTHGATE | PINE HOLLOW</div>

  <div class="social" aria-label="Social media">
    <span></span><span></span><span></span><span></span>
  </div>

  <div class="partner">Marlow Fenwick</div>
</section>

</body>
</html>
```